NZ First of it's kind solutions directory and marketplace for busy Mums needs a business card design

We need a business card design for our new nationwide business in NZ (long term plans to go global). We provide solutions to the everyday challenges that busy Mums face by connecting them with quality communities and suppliers of carefully selected, relevant products and services. We sell direct via our online marketplace. The final design should communicate our values of inclusivity, quality and smart solutions. Colours should incorporate our logo colour palette of #477077 and #6ba8b2. Our website is at https://www.brightnestmums.example

Target Market(s)

busy Mums, Age 28 – 50, female, income over $100K, location main centres NZ primarily but NZ wide. Is likely juggling work or career with a young family. Probably had hobbies which have fallen by the wayside.
-Wants to succeed in her chosen career without compromising on family life
-to successfully juggle her career without feeling like she is compromising her children
- Is time poor, something always has to give and it’s generally her health (she’ll stay up late, get stressed)
- probably ex corporate or professional career. Has discretional income

Industry/Entity Type

Business

Contact Information for Business Card

Lena Forbisher, Founder, BrightNestMums.example (Strapline Tap; Gather; Sorted), 47 Kowhai Terrace, Ellerslie, Auckland 1051, New Zealand. Mob: 021 483 517 Ph: +64 (0)9 571 4860

Font styles to use
Other font styles liked:
• Raleway, and/or Architects Daughter

Colors
00a990
33b8a4
86cfc6
cfeae6

Requirements
Must have
• the above details, streamline. the logo and colours associated with those logos
Should not have
• foil or metallic colours

```html
<!DOCTYPE html>
<html lang="en">
<head>
<meta charset="utf-8">
<title>BrightNestMums – Business Card</title>
<link rel="stylesheet" href="https://fonts.googleapis.com/css2?family=Nunito:wght@700;800&family=Roboto+Condensed:ital,wght@0,400;1,400&display=swap">
<style>
  :root {
    --teal-dark: #477077;
    --teal-deep: #3d5f66;
    --teal-light: #6ba8b2;
    --card-white: #f4f4f4;
    --page-bg: #e6e6e6;
    --text-light: #ffffff;
    --text-soft: #e4eef0;
  }
  * { margin: 0; padding: 0; box-sizing: border-box; }
  html, body {
    width: 1200px; height: 576px; overflow: hidden;
    background: var(--page-bg);
  }
  .canvas { position: relative; width: 1200px; height: 576px; }

  .card {
    position: absolute;
    top: 138px;
    width: 484px; height: 293px;
    border-radius: 12px;
    overflow: hidden;
    box-shadow: 0 3px 6px rgba(0,0,0,0.18);
  }
  .card--front { left: 82px; background: var(--card-white); }
  .card--back  { left: 602px; width: 480px; background: var(--teal-dark); }

  /* front */
  .brand {
    position: absolute; left: 34px; top: 128px;
    display: flex; align-items: center; gap: 10px;
  }
  .brand__dot {
    width: 22px; height: 22px; border-radius: 50%;
    background: var(--teal-dark);
  }
  .brand__name {
    font-family: "Nunito", sans-serif; font-weight: 800;
    font-size: 25px; letter-spacing: -0.3px;
    color: var(--teal-dark);
  }
  .strapline {
    position: absolute; left: 77px; top: 165px;
    font-family: "Roboto Condensed", sans-serif;
    font-size: 9px; letter-spacing: 3px;
    color: var(--teal-deep);
  }
  .strapline__sep { color: var(--teal-light); padding: 0 5px; }
  .feature-art {
    position: absolute; right: 0; top: 18px; bottom: 0;
    width: 200px;
    background: linear-gradient(160deg, var(--teal-light) 0%, var(--teal-dark) 45%, var(--teal-deep) 100%);
  }

  /* back */
  .identity {
    position: absolute; right: 260px; top: 112px;
    text-align: right; color: var(--text-light);
    font-family: "Roboto Condensed", sans-serif;
  }
  .identity__name {
    font-family: "Nunito", sans-serif; font-weight: 800;
    font-size: 20px; line-height: 24px;
  }
  .identity__role { font-style: italic; font-size: 12.5px; line-height: 16px; color: var(--text-soft); }
  .identity__address { margin-top: 8px; font-size: 12.5px; line-height: 18px; color: var(--text-soft); }

  .contact-list {
    position: absolute; left: 244px; top: 114px;
    list-style: none;
    font-family: "Roboto Condensed", sans-serif;
    font-size: 12.5px; color: var(--text-soft);
  }
  .contact-list__item { display: flex; align-items: center; gap: 9px; height: 18.5px; }
  .contact-list__icon { width: 10px; height: 10px; fill: var(--text-light); flex: none; }
</style>
</head>
<body>
<div class="canvas">

  <section class="card card--front">
    <div class="brand">
      <span class="brand__dot"></span>
      <span class="brand__name">BrightNestMums</span>
    </div>
    <p class="strapline">TAP<span class="strapline__sep">|</span>GATHER<span class="strapline__sep">|</span>SORTED</p>
    <div class="feature-art" role="img" aria-label="Large brand illustration in teal tones"></div>
  </section>

  <section class="card card--back">
    <div class="identity">
      <h1 class="identity__name">Lena Forbisher</h1>
      <p class="identity__role">Founder</p>
      <p class="identity__address">47 Kowhai Terrace, Ellerslie,<br>Auckland 1051, New Zealand</p>
    </div>
    <ul class="contact-list">
      <li class="contact-list__item">
        <svg class="contact-list__icon" viewBox="0 0 10 10"><path d="M2.5 0h5a1 1 0 0 1 1 1v8a1 1 0 0 1-1 1h-5a1 1 0 0 1-1-1V1a1 1 0 0 1 1-1zM3 1.5v6h4v-6zM5 8.2a.5.5 0 1 0 0 1 .5.5 0 0 0 0-1z"/></svg>
        021 483 517
      </li>
      <li class="contact-list__item">
        <svg class="contact-list__icon" viewBox="0 0 10 10"><path d="M0 3.5C0 2 2 1 5 1s5 1 5 2.5V4H7.5V3H2.5v1H0zM2 5h6l1 4H1zM5 5.8a1.4 1.4 0 1 0 0 2.8 1.4 1.4 0 0 0 0-2.8z"/></svg>
        +64 (0)9 571 4860
      </li>
      <li class="contact-list__item">
        <svg class="contact-list__icon" viewBox="0 0 10 10"><path d="M0 2h10v6H0zM.8 2.6 5 5.6l4.2-3H.8z"/></svg>
        www.BrightNestMums.example
      </li>
      <li class="contact-list__item">
        <svg class="contact-list__icon" viewBox="0 0 10 10"><path d="M5 0a5 5 0 1 0 0 10A5 5 0 0 0 5 0zm0 1c.6 0 1.3 1.4 1.4 3.5H3.6C3.7 2.4 4.4 1 5 1zM1.1 4.5a4 4 0 0 1 1.9-3 7.5 7.5 0 0 0-.4 3zm5.9-3a4 4 0 0 1 1.9 3H7.4a7.5 7.5 0 0 0-.4-3zM1.1 5.5h1.5c0 1.1.2 2.2.4 3a4 4 0 0 1-1.9-3zm2.5 0h2.8C6.3 7.6 5.6 9 5 9s-1.3-1.4-1.4-3.5zm3.8 0h1.5A4 4 0 0 1 7 8.5c.2-.8.4-1.9.4-3z"/></svg>
        lenaforbisher@brightnestmums.example
      </li>
    </ul>
  </section>

</div>
</body>
</html>
```